Velmora Wheel Outings company needs new Web Design

We need a new design for our main website. You can find the wireframe(file # 12) for the homepage in uploaded files. Firstly we want a design for the homepage (Please take a look at last uploaded file #12 for more information). If we like it we would also need designs for other subpages (section detail page, tour detail page, reservation form, FAQ, photogallery, search results, blog and basic content page). All wireframes are ready, we need design, graphics, colors ideas.
Our current page is: http://www.tovarkolo.cz. The logo and information content should remain the same.
Updates

Notes for Tovarkolo.cz  -new web site 2014

 

There is new file uploaded with notes. Its a draft But Its just square boxes, and boring..we need some creativity, some curves, shapes…. Motions.

Bikes elements could be used, wheel shapes.. 

Web site should show that bikes is the best way of getting around, itsecological, green, fun and healthy. 

The new file is uploaded for more explanation, ideas, layouts and notes.

Reason: We still dont see the good interesting design ideas.

Reason: New updates in uploaded file #12.

We are looking for an exciting  original design; bike parts as chain, wheels, frames, nature elements.. can be used as borders for blocks. Decent background with bike wheel traces, or bike elements, some graphic and fun stuff to show that its not just a bike shop But bike tour company providing fun, active and informational experience!

Also check the updated brief and file#12.

Reason: Not available for close communication from Dec 7 till Dec 13

Reason: Winter holidays

Target Market(s)

Our customers are mostly tourists visiting Prague interested in active, informational and fun way to see the city; including big student and company groups, families, independent travelers; age from 16 to 75. Please take a look at last uploaded file #12 for more information.

Industry/Entity Type

It Company

Requirements
Must have
• Exciting original design, bike parts as chain, wheel.. can be used as borders for blocks. Decent background with bike wheel traces, or bike elements, some graphic and fun stuff to show that its not just a bike shop But bike tour company providing fun, active and informational experience!
Nice to have
• -web visitors should easily see the different kind of services/tours we offer
-impression should be sporty/active but not too much as our services are suitable for people who are not active on daily bases as well using the bike as the way of transportation not as the sport/adrenalin tool.

```html
<!DOCTYPE html>
<html lang="en">
<head>
<meta charset="utf-8">
<title>Velmora Wheels – Guided Bike Tours &amp; Rentals</title>
<link rel="stylesheet" href="https://fonts.googleapis.com/css2?family=Electrolize&family=Russo+One&display=swap">
<style>
:root{
  --orange:#ef8420;--orange-dark:#c8661a;
  --green:#8aaa22;--green-h:#5d7a1a;--green-1:#4e6a17;--green-2:#415a13;--green-3:#344a0f;
  --blue:#4fb0da;--blue-h:#3a87a8;--blue-1:#316f8b;--blue-2:#295f78;--blue-3:#1f4d62;
  --rust:#e8821e;--rust-h:#b96516;--rust-1:#9a5313;--rust-2:#7f4410;--rust-3:#6a380c;
  --map-light:#ebe8e1;--map-mid:#dcd7cc;--map-road:#f7f5f0;--pin:#d8321e;
  --ink:#333;--muted:#777;--panel:#fff;
}
*{box-sizing:border-box;margin:0;padding:0}
html,body{width:886px;height:1200px;overflow:hidden}
body{position:relative;font-family:"Electrolize",sans-serif;color:var(--ink);
  background:linear-gradient(180deg,#7fa3b8 0%,#b9cf9a 14%,#6f9a3a 26%,#3f5a22 36%,#2a2318 46%,#1a1410 60%,#140f0c 100%)}
.card{position:absolute;left:129px;width:629px;background:var(--panel);border-radius:4px;box-shadow:0 2px 10px rgba(0,0,0,.35)}
.header{top:15px;height:347px}
.logo-mark{position:absolute;left:17px;top:11px;width:64px;height:64px;border-radius:50%;background:var(--orange)}
.brand{position:absolute;left:90px;top:32px;font-size:22px;color:var(--orange)}
.tagline{position:absolute;left:91px;top:60px;font-size:8px;color:var(--muted);letter-spacing:.3px}
.search{position:absolute;left:469px;top:13px;width:146px;height:21px;border-radius:11px;background:var(--orange);box-shadow:inset 0 1px 2px rgba(0,0,0,.2)}
.search span{position:absolute;left:3px;top:3px;width:118px;height:15px;border-radius:8px;background:#fff}
.search svg{position:absolute;right:7px;top:4px}
.social{position:absolute;top:49px;font-size:15px;color:#2d4a8a}
.social.notes{color:#222;font-size:13px;top:51px}
.flags{position:absolute;left:518px;top:51px;display:flex;gap:5px}
.flags i{display:block;width:19px;height:14px;border:1px solid #ccc}
.nav{position:absolute;left:0;top:78px;width:629px;height:28px;background:var(--orange);display:flex}
.nav a{flex:1;color:#fff;text-decoration:none;font-size:11px;display:flex;align-items:center;justify-content:center;border-left:1px solid rgba(255,255,255,.35)}
.nav a:first-child{flex:0 0 112px;background:#fff;color:var(--orange);border:0}
.dropdown{position:absolute;left:0;top:106px;width:112px;background:#fff;z-index:3;box-shadow:0 2px 4px rgba(0,0,0,.2)}
.dropdown a{display:block;height:24px;line-height:24px;text-align:center;font-size:9px;color:#555;border-bottom:1px solid #e5e5e5;text-decoration:none}
.dropdown a.active{background:#eee;color:var(--orange)}
.slider{position:absolute;left:7px;top:139px;width:353px;height:202px;background:linear-gradient(180deg,#8fb3c8 0%,#a9b79a 45%,#d9d3c8 100%)}
.slider h2{position:absolute;left:0;right:0;top:118px;text-align:center;font-family:"Russo One",sans-serif;font-weight:400;font-size:25px;color:var(--orange)}
.slider p{position:absolute;left:0;right:0;top:148px;text-align:center;font-size:12px;color:#111}
.pager{position:absolute;left:60px;top:166px;display:flex}
.pager span{width:45px;height:26px;background:#2a2a2a;color:#fff;font-size:12px;display:flex;align-items:center;justify-content:center;border-right:1px solid #444}
.pager span.on{background:var(--orange)}
.video{position:absolute;left:368px;top:139px;width:255px;height:202px;background:#000}
.video .bar{position:absolute;left:0;right:0;bottom:0;height:18px;background:#1a1a1a}
.main{top:387px;height:734px}
.col{position:absolute;top:16px;width:191px;height:306px}
.col h3{height:25px;line-height:25px;text-align:center;font-weight:400;font-size:15px;color:#fff}
.col .photo{margin:5px 4px 0;height:102px}
.col .blurb{height:64px;padding:8px 10px 0;font-size:8.5px;line-height:12px;text-align:center;color:#fff}
.col h4{height:29px;line-height:29px;text-align:center;font-weight:400;font-size:13px;color:#111;box-shadow:inset 0 1px 0 rgba(255,255,255,.3)}
.col a{display:block;height:26px;line-height:26px;text-align:center;font-size:10.5px;color:#fff;text-decoration:none}
.col.city{left:15px;background:var(--green)}.city h4{background:var(--green-h)}.city a:nth-of-type(1){background:var(--green-1)}.city a:nth-of-type(2){background:var(--green-2)}.city a:nth-of-type(3){background:var(--green-3)}
.col.country{left:219px;background:var(--blue)}.country h4{background:var(--blue-h)}.country a:nth-of-type(1){background:var(--blue-1)}.country a:nth-of-type(2){background:var(--blue-2)}.country a:nth-of-type(3){background:var(--blue-3)}
.col.rental{left:424px;background:var(--rust)}.rental h4{background:var(--rust-h)}.rental a:nth-of-type(1){background:var(--rust-1)}.rental a:nth-of-type(2){background:var(--rust-2)}.rental a:nth-of-type(3){background:var(--rust-3)}
.map{position:absolute;left:15px;top:352px;width:352px;height:202px;overflow:hidden;
  background:radial-gradient(ellipse at 45% 55%,var(--map-road) 0%,var(--map-light) 45%,var(--map-mid) 100%)}
.map svg{position:absolute;left:162px;top:84px}
.address{position:absolute;left:381px;top:352px;width:232px;height:202px;background:linear-gradient(135deg,#e06a10,#c9520c);color:#fff;text-align:center}
.address svg{margin-top:14px}
.address h3{font-weight:400;font-size:15px;line-height:17px;margin-top:6px;letter-spacing:.5px}
.address p{font-size:12px;line-height:16px;margin-top:14px}
.promo{position:absolute;top:587px;height:126px}
.badge{left:15px;width:163px;background:#5aa53a}
.badge i{position:absolute;left:43px;top:25px;width:76px;height:76px;border-radius:50%;background:#fff;opacity:.85}
.offer{left:192px;width:162px;background:linear-gradient(135deg,#dfe7f0,#8aa3c0)}
.offer .t{position:absolute;left:8px;top:7px;font-family:"Russo One",sans-serif;line-height:1}
.offer .t b{display:block;font-weight:400;color:#d8261a}
.team{left:370px;width:145px;background:linear-gradient(180deg,#f5a21a,#d9530a 60%,#3a1a08)}
.team span{position:absolute;left:0;right:0;bottom:5px;text-align:center;font-family:"Russo One",sans-serif;font-size:12px;color:#fff}
.rider{position:absolute;left:526px;top:560px;width:96px;height:164px;background:linear-gradient(180deg,#f4f4f4,#dedede);border-radius:6px}
.footer{top:1146px;height:33px;display:flex;align-items:center;padding:0 15px;font-size:9px}
.footer nav{display:flex;gap:20px;color:var(--muted)}
.footer nav a{color:inherit;text-decoration:none}
.footer nav a:first-child{color:#111}
.footer small{margin-left:auto;font-size:9px;color:#111}
</style>
</head>
<body>
<header class="card header">
  <span class="logo-mark"></span>
  <div class="brand">Velmora Wheels</div>
  <div class="tagline">GUIDED BIKE TOURS &amp; RENTALS</div>
  <div class="search"><span></span>
    <svg width="10" height="10" viewBox="0 0 10 10"><circle cx="4" cy="4" r="3" fill="none" stroke="#fff" stroke-width="1.5"/><line x1="6.2" y1="6.2" x2="9" y2="9" stroke="#fff" stroke-width="1.5"/></svg>
  </div>
  <div class="social" style="left:323px">Chatterbox</div>
  <div class="social notes" style="left:415px">TripNotes</div>
  <div class="flags"><i style="background:#b22234"></i><i style="background:#7fb0de"></i><i style="background:#3a9a4a"></i><i style="background:#1a8a3a"></i></div>
  <nav class="nav"><a>Bike Tours</a><a>Private Tours</a><a>About</a><a>Blog</a><a>Contact</a><a>Reservation</a></nav>
  <div class="dropdown"><a>City Classic</a><a class="active">Country Tours</a><a>Bike Rental</a></div>
  <div class="slider">
    <div role="img" aria-label="Group of smiling cyclists riding through a leafy street" style="position:absolute;inset:0"></div>
    <h2>Prauge Speed Tour</h2>
    <p>Classic Speed Tour • Old Prauge speed tour</p>
    <div class="pager"><span>1</span><span class="on">2</span><span>3</span><span>4</span><span>5</span></div>
  </div>
  <div class="video" role="img" aria-label="Embedded tour video player">
    <svg style="position:absolute;left:117px;top:86px" width="14" height="16"><polygon points="0,0 14,8 0,16" fill="#fff"/></svg>
    <div class="bar"></div>
  </div>
</header>

<main class="card main">
  <section class="col city">
    <h3>City Tours</h3>
    <div class="photo" role="img" aria-label="Cyclist riding through a busy city street" style="background:linear-gradient(135deg,#8c8a86,#4a4f55)"></div>
    <p class="blurb">Lorem ipsum dolor sit amet, consectetur adipiscing elit. Nulla lobortis consequat mauris, eget eleifend nunc viverra viverra. Ut ac risus odio.</p>
    <h4>Bestseller Tours</h4>
    <a>Classic City Bike Tour</a><a>Panoramic Bike Tour</a><a>Beer Garden Tour</a>
  </section>
  <section class="col country">
    <h3>Country Tours</h3>
    <div class="photo" role="img" aria-label="Couple cycling together on a country outing" style="background:linear-gradient(135deg,#c88a6a,#7a4a4a)"></div>
    <p class="blurb">Lorem ipsum dolor sit amet, consectetur adipiscing elit. Nulla lobortis consequat mauris, eget eleifend nunc viverra viverra. Ut ac risus odio.</p>
    <h4>Recommended Tours</h4>
    <a>Tour to Karistejn Castle</a><a>Prague Troja Tour</a><a>Parague - Dresden Tour</a>
  </section>
  <section class="col rental">
    <h3>Bike Rental</h3>
    <div class="photo" role="img" aria-label="Row of rental bicycles parked at a stand" style="background:linear-gradient(135deg,#d8dde2,#6f7880)"></div>
    <p class="blurb">Lorem ipsum dolor sit amet, consectetur adipiscing elit. Nulla lobortis consequat mauris, eget eleifend nunc viverra viverra. Ut ac risus odio.</p>
    <h4>You might also like</h4>
    <a>Self-guided Tours</a><a>Private Tours</a><a>Team Bike Tours</a>
  </section>

  <div class="map" role="img" aria-label="Street map of the old town with a marker at the meeting point">
    <svg width="18" height="26" viewBox="0 0 18 26"><path d="M9 1a8 8 0 0 0-8 8c0 6 8 16 8 16s8-10 8-16a8 8 0 0 0-8-8z" fill="var(--pin)"/><circle cx="9" cy="9" r="3" fill="#fff"/></svg>
  </div>
  <div class="address">
    <svg width="16" height="24" viewBox="0 0 16 24"><path d="M8 1a7 7 0 0 0-7 7c0 5 7 15 7 15s7-10 7-15a7 7 0 0 0-7-7z" fill="none" stroke="#fff" stroke-width="1.6"/><circle cx="8" cy="8" r="2.5" fill="#fff"/></svg>
    <h3>OUR ADDRESS &amp;<br>MEETING POINT:</h3>
    <p>Lipová 12, Prague 1<br>Open Daily: 09:00 - 21:00</p>
    <p>Email: info@tovarkolo.cz<br>Tel: +420 600 555 014</p>
  </div>

  <div class="promo badge" role="img" aria-label="Travel review partner badge"><i></i></div>
  <div class="promo offer" role="img" aria-label="Cyclist riding a road bike with a special offer">
    <div class="t" style="font-size:12px"><b style="font-size:12px">Special</b><b style="font-size:19px">Offer</b>
      <span style="display:block;font-size:11px;color:#111;margin-top:2px">Book Your<br>trip now<br>and get</span>
      <b style="font-size:19px">30%<br>OFF</b></div>
  </div>
  <div class="promo team" role="img" aria-label="Group of cyclists silhouetted against a sunset"><span>Team Bike Tours</span></div>
  <div class="rider" role="img" aria-label="Smiling rider in a helmet standing with a white bicycle"></div>
</main>

<footer class="card footer">
  <nav><a>Home</a><a>Private Tours</a><a>Photos</a><a>FAQ</a><a>Reservation</a><a>Links</a><a>Contact</a></nav>
  <small>Copyrightn 2013 Tovarkolo</small>
</footer>
</body>
</html>
```